Real Estate Website

Please refer to the attached document. It will be for a real estate agency specialising in commercial and residential sales. looking for Modern and minimalist, Sleek, professional, premium feel

```html
<!DOCTYPE html>
<html lang="en">
<head>
<meta charset="utf-8">
<title>Castellan Group — Commercial & Residential Property</title>
<link rel="stylesheet" href="https://fonts.googleapis.com/css2?family=Outfit:wght@400;500;600;700;800&family=Poppins:wght@400;500;600&display=swap">
<style>
:root{
  --orange:#F0522E;
  --orange-soft:#F6794F;
  --navy:#243240;
  --navy-deep:#1C2833;
  --ink:#1F2A35;
  --text:#5B6470;
  --muted:#8A929C;
  --line:#E4E7EB;
  --grey-bg:#F4F5F7;
  --white:#FFFFFF;
  --star:#F5A623;
}
*{box-sizing:border-box;margin:0;padding:0}
html,body{width:1200px;height:5277px;overflow:hidden}
body{position:relative;background:var(--white);font-family:"Poppins",sans-serif;color:var(--text);font-size:12.5px;line-height:22px}
.abs{position:absolute}
h1,h2,h3,h4,.heading{font-family:"Outfit",sans-serif;color:var(--ink)}
.accent{color:var(--orange)}
.section-label{font-family:"Outfit",sans-serif;font-size:12.5px;font-weight:600;letter-spacing:.5px;color:var(--ink);display:flex;align-items:center;gap:8px;text-transform:uppercase}
.section-label::before{content:"";width:11px;height:11px;border-radius:50%;background:var(--orange)}
.section-title{font-size:24px;font-weight:600;line-height:32px}
.center{left:0;width:1200px;text-align:center;justify-content:center}
.btn{display:inline-flex;align-items:center;gap:8px;font-family:"Outfit",sans-serif;font-size:12.5px;font-weight:500;color:#fff;border-radius:3px;padding:0 18px;height:38px}
.btn-dark{background:var(--navy)}
.btn-orange{background:var(--orange)}
.btn svg{width:11px;height:11px}

/* header */
.site-header{top:0;left:0;width:1200px;height:98px;background:#fff}
.brand{display:flex;align-items:center;gap:10px;font-family:"Outfit",sans-serif;font-weight:700;font-size:27px;color:var(--ink)}
.brand-dot{width:26px;height:26px;border-radius:50%;background:var(--orange)}
.main-nav{left:338px;top:40px;display:flex;gap:28px;font-family:"Outfit",sans-serif;font-size:11.5px;font-weight:600;color:var(--ink)}
.contact-btn{left:981px;top:33px;width:123px;height:39px;background:var(--orange);color:#fff;font-family:"Outfit",sans-serif;font-size:11.5px;font-weight:600;display:flex;align-items:center;justify-content:center;border-radius:2px}

/* hero */
.hero{top:98px;left:0;width:1200px;height:562px;background:linear-gradient(100deg,#1d2b3c 0%,#2c4b6e 35%,#3b78a8 62%,#8fc3e4 80%,#2b5c86 100%)}
.hero-shade{inset:0;background:linear-gradient(90deg,rgba(16,24,36,.75) 0%,rgba(16,24,36,.35) 55%,rgba(16,24,36,0) 100%)}
.hero h1{left:143px;top:112px;width:520px;font-size:40px;line-height:51px;font-weight:800;color:#fff}
.hero p{left:143px;top:325px;width:400px;font-size:15px;line-height:25px;color:#fff}
.hero .btn{left:143px;top:406px;height:37px;width:181px;justify-content:center;font-size:11.5px}
.scroll-cue{left:565px;top:625px;width:70px;height:70px;border-radius:50%;background:#fff;box-shadow:0 6px 18px rgba(0,0,0,.12);display:flex;align-items:center;justify-content:center}

/* appraisal */
.appraisal-photo{left:141px;top:754px;width:418px;height:383px;border-radius:14px;background:linear-gradient(135deg,#7c8a98 0%,#c9b7a4 45%,#eae3da 100%)}
.appraisal-text{left:600px;top:756px;width:520px}
.appraisal-text h2{font-size:24px;font-weight:600;margin:16px 0 12px;line-height:32px}
.appraisal-text p{margin-bottom:11px}

/* services */
.services{top:1229px;left:0;width:1200px;height:495px;background:var(--grey-bg)}
.service-card{top:171px;width:282px;height:239px;background:#fff;border:1px solid var(--line);border-radius:4px;padding:20px 18px}
.service-card .icon{width:52px;height:52px;border-radius:50%;background:var(--navy);display:flex;align-items:center;justify-content:center;margin-bottom:22px}
.service-card h3{font-size:16px;font-weight:600;margin-bottom:8px}
.service-card p{font-size:12.2px}
.service-card.featured{background:linear-gradient(160deg,#F6794F,#E94C29);border-color:var(--orange)}
.service-card.featured::after{content:"";position:absolute;inset:8px;border:1px solid rgba(255,255,255,.55);border-radius:3px}
.service-card.featured .icon{background:#fff}
.service-card.featured h3,.service-card.featured p{color:#fff}

/* stats */
.stats{top:1724px;left:0;width:1200px;height:209px;background:linear-gradient(90deg,#3a4654,#56616d 50%,#3c4856)}
.stat{top:62px;color:#fff}
.stat strong{display:block;font-family:"Outfit",sans-serif;font-size:50px;font-weight:600;line-height:56px}
.stat span{font-size:14px}
.stats-notch{left:584px;top:1932px;width:0;height:0;border-left:16px solid transparent;border-right:16px solid transparent;border-top:16px solid #3f4a58}

/* why choose */
.why-item{width:270px}
.why-item h4{font-size:15px;font-weight:600;margin-bottom:4px}
.why-item p{font-size:12px;line-height:20px}
.why-item.left{text-align:right}
.why-icon{width:46px;height:46px;border-radius:50%;background:#fff;box-shadow:0 3px 12px rgba(0,0,0,.1);display:flex;align-items:center;justify-content:center}
.emblem{left:471px;top:2136px;width:256px;height:256px;border-radius:50%;background:#fff;box-shadow:0 8px 30px rgba(240,82,46,.15);display:flex;align-items:center;justify-content:center}
.emblem::before{content:"";position:absolute;inset:20px;border-radius:50%;border:1.5px dashed var(--orange-soft)}
.emblem .brand{font-size:30px;flex-direction:column;gap:10px}

/* about */
.about-text{left:143px;top:2609px;width:460px}
.about-text h2{font-size:24px;font-weight:600;margin:14px 0 10px;line-height:32px}
.about-text p{margin-bottom:12px}
.about-photo{left:641px;top:2605px;width:418px;height:348px;border-radius:3px;background:linear-gradient(135deg,#9aa6b2,#d6dde4 55%,#eef1f4)}
.divider{left:141px;top:3031px;width:918px;height:1px;background:var(--line)}

/* testimonials */
.review{top:3205px;width:281px;height:301px;background:#fff;border-radius:4px;box-shadow:0 4px 20px rgba(20,30,40,.08);padding:20px 22px}
.quote{width:36px;height:36px;border-radius:50%;background:var(--orange);color:#fff;font-family:"Outfit",sans-serif;font-size:28px;font-weight:700;display:flex;align-items:center;justify-content:center;line-height:1;padding-top:10px}
.review .rating{display:flex;justify-content:space-between;align-items:center;margin:8px 0 10px}
.stars{color:var(--star);font-size:17px;letter-spacing:2px}
.source-mark{width:18px;height:18px;border-radius:50%;border:2px solid var(--muted)}
.review p{font-size:12.2px;line-height:22px}
.review hr{width:40px;border:none;height:1.5px;background:var(--orange);margin:16px 0 12px}
.review h4{font-size:14px;font-weight:600;line-height:20px}
.review span{font-size:12px}
.carousel-arrow{top:3352px;width:26px;height:26px;border-radius:50%;display:flex;align-items:center;justify-content:center}
.dots{top:3534px;left:568px;display:flex;gap:8px}
.dots i{width:7px;height:7px;border-radius:50%;background:#CDD1D6}
.dots i.on{background:var(--orange)}

/* property split */
.property{top:3629px;left:0;width:1200px;height:611px;background:var(--grey-bg)}
.split-card{width:438px;height:332px;border-radius:4px;padding:38px 28px;color:#fff}
.split-card h3{color:#fff;font-size:20px;font-weight:600;margin-bottom:8px}
.split-card .sub{font-size:12px;line-height:20px;margin-bottom:12px}
.split-card ul{list-style:none}
.split-card li{display:flex;align-items:center;gap:9px;font-size:12.5px;height:34px}
.tick{width:18px;height:18px;border-radius:50%;background:#fff;display:flex;align-items:center;justify-content:center;flex:none}
.card-commercial{left:154px;top:174px;background:linear-gradient(150deg,#F26A42,#E9502D)}
.card-commercial .sub{color:#FFE2D8}
.card-residential{left:608px;top:205px;background:linear-gradient(150deg,#3a4858,#2b3846)}
.card-residential .sub{color:#D7DEE5}
.split-badge{left:578px;top:3961px;width:44px;height:44px;border-radius:50%;background:#fff;box-shadow:0 3px 12px rgba(0,0,0,.15);display:flex;align-items:center;justify-content:center}

/* contact form */
.form-box{left:141px;top:4331px;width:477px;height:441px;border:1px solid var(--line);border-radius:4px;padding:38px 29px 0}
.form-box label{display:block;font-family:"Outfit",sans-serif;font-size:13px;font-weight:500;color:var(--ink);margin-bottom:6px}
.field{height:39px;background:#F1F2F4;border-radius:3px;margin-bottom:24px}
.field.tall{height:105px;margin-bottom:22px}
.submit{height:45px;background:var(--navy);color:#fff;font-family:"Outfit",sans-serif;font-weight:600;font-size:13px;display:flex;align-items:center;justify-content:center;border-radius:3px}
.move-text{left:651px;top:4400px;width:420px}
.move-text h2{font-size:22px;font-weight:600;line-height:30px;margin-bottom:6px}
.move-text > p{font-size:12px;line-height:21px;margin-bottom:30px}
.move-text h3{font-size:17px;font-weight:600;margin-bottom:10px}
.perk{display:flex;gap:12px;margin-bottom:16px}
.perk h4{font-size:12.5px;font-weight:600;line-height:20px}
.perk p{font-size:12px;line-height:20px}

/* footer */
.site-footer{top:4854px;left:0;width:1200px;height:423px;background:var(--navy)}
.footer-bump{left:530px;top:4806px;width:140px;height:96px;border-radius:0 0 70px 70px;background:#fff}
.to-top{left:585px;top:4858px}
.footer-col h4{color:#fff;font-size:15px;font-weight:600;margin-bottom:14px}
.footer-col ul{list-style:none}
.footer-col li{color:#D6DCE2;font-size:12.5px;line-height:29px}
.footer-col li::before{content:"›";color:var(--orange);margin-right:6px}
.footer-about{left:143px;top:4966px;width:230px;color:#C9D0D7;font-size:12.5px;line-height:21px}
.footer-about .brand{color:#fff;font-size:30px;margin-bottom:34px}
.follow{display:flex;align-items:center;gap:8px;margin-top:34px;color:#fff}
.follow i{width:20px;height:20px;border-radius:50%;background:#fff;display:inline-block}
.follow i.on{background:var(--orange)}
.contact-line{display:flex;gap:14px;align-items:flex-start;color:#D6DCE2;font-size:12.5px;line-height:21px;margin-bottom:20px}
.contact-icon{width:30px;height:30px;border-radius:50%;background:var(--orange);display:flex;align-items:center;justify-content:center;flex:none}
.contact-icon.light{background:rgba(255,255,255,.12)}
.copyright{left:0;top:5238px;width:1200px;text-align:center;color:#C9D0D7;font-size:11.5px;border-top:1px solid rgba(255,255,255,.12);padding-top:12px}
</style>
</head>
<body>

<header class="abs site-header">
  <div class="abs brand" style="left:98px;top:34px;font-size:26px"><span class="brand-dot"></span>Castellan Group</div>
  <nav class="abs main-nav">
    <span>HOME</span><span>COMMERCIAL/INDUSTRIAL</span><span>RESIDENTIAL</span><span>BUSINESS SALES</span><span>ABOUT US</span><span>INFO ⌄</span>
  </nav>
  <a class="abs contact-btn">CONTACT US</a>
</header>

<section class="abs hero" role="img" aria-label="Glass office towers with reflective blue facades">
  <div class="abs hero-shade"></div>
  <h1 class="abs">Specialists in Commercial/ Industrial Property, Trusted in Residential Property</h1>
  <p class="abs">Maximising returns, protecting investments, expert property advisory</p>
  <a class="abs btn btn-orange">BOOK AN APPRAISAL</a>
</section>
<div class="abs scroll-cue">
  <svg width="16" height="16" viewBox="0 0 16 16" fill="none" stroke="#243240" stroke-width="1.6"><path d="M4 4l4 4 4-4M4 9l4 4 4-4"/></svg>
</div>

<div class="abs appraisal-photo" role="img" aria-label="Three colleagues reviewing a property report on a laptop"></div>
<div class="abs appraisal-text">
  <div class="section-label">Book an Appraisal</div>
  <h2>Discover The Real Value Of <span class="accent">Your Property</span></h2>
  <p>At Castellan Group, we don't just provide standard appraisals — we deliver strategic, insight-driven reports that uncover the true drivers of your property's worth. Whether it's commercial, industrial, or residential, our expertise ensures you see the full picture.</p>
  <p>From market trends and rental potential to investment performance and future growth opportunities, our tailored reports give you clarity, confidence, and actionable insights.</p>
  <p>Book a confidential consultation today and gain the expert guidance you need to maximise returns and make smarter property decisions.</p>
  <a class="btn btn-dark" style="margin-top:16px">Schedule Consultation <svg viewBox="0 0 12 12" fill="none" stroke="#fff" stroke-width="1.4"><path d="M3 9l6-6M4 3h5v5"/></svg></a>
</div>

<section class="abs services">
  <div class="abs section-label center" style="top:86px">What We Do</div>
  <h2 class="abs section-title center" style="top:109px">Property Management, <span class="accent">Sales &amp; Leasing</span></h2>
  <article class="abs service-card" style="left:141px">
    <div class="icon"><svg width="24" height="24" viewBox="0 0 24 24" fill="none" stroke="#fff" stroke-width="1.5"><rect x="5" y="3" width="11" height="18"/><path d="M16 9h4v12H3M8 7h2M11 7h2M8 11h2M11 11h2M8 15h2M11 15h2"/></svg></div>
    <h3>Commercial &amp; Industrial</h3>
    <p>Specialist management and leasing of premium commercial and industrial assets, trusted by investors and developers.</p>
  </article>
  <article class="abs service-card featured" style="left:459px">
    <div class="icon"><svg width="24" height="24" viewBox="0 0 24 24" fill="none" stroke="#F0522E" stroke-width="1.6"><path d="M3 11l9-7 9 7M5 10v10h14V10M10 20v-5h4v5"/></svg></div>
    <h3>Residential Property</h3>
    <p>Expert residential property management and sales services with proven results and exceptional client outcomes.</p>
  </article>
  <article class="abs service-card" style="left:776px">
    <div class="icon"><svg width="24" height="24" viewBox="0 0 24 24" fill="none" stroke="#fff" stroke-width="1.6"><path d="M12 3l7 3v6c0 4-3 7-7 9-4-2-7-5-7-9V6z"/><path d="M9 12l2 2 4-4"/></svg></div>
    <h3>Property Advisory</h3>
    <p>Comprehensive financial reporting, budgeting, and expense management to optimize cash flow and returns.</p>
  </article>
</section>

<section class="abs stats" role="img" aria-label="Muted city skyline behind key figures">
  <div class="abs stat" style="left:143px"><strong>30+</strong><span>Years Experience</span></div>
  <div class="abs stat" style="left:414px"><strong>98%</strong><span>Success Rate</span></div>
  <div class="abs stat" style="left:684px"><strong>1K+</strong><span>Happy Customer</span></div>
  <div class="abs stat" style="left:932px"><strong>250+</strong><span>Businesses Sold</span></div>
</section>
<div class="abs stats-notch"></div>

<div class="abs section-label center" style="top:2038px">Why Choose Us</div>
<h2 class="abs section-title center" style="top:2070px">Commercial &amp; Industrial Property <span class="accent">Management &amp; Leasing</span></h2>

<div class="abs why-item left" style="left:111px;top:2152px"><h4>Sector Expertise</h4><p>Deep knowledge across medical, healthcare, franchise, retail, and industrial sectors, enabling tailored strategies for each asset class.</p></div>
<div class="abs why-icon" style="left:405px;top:2168px"><svg width="22" height="22" viewBox="0 0 24 24" fill="none" stroke="#243240" stroke-width="1.4"><circle cx="12" cy="12" r="9"/><path d="M12 7l1.5 3.2 3.5.4-2.6 2.4.7 3.4L12 14.8 8.9 16.4l.7-3.4L7 10.6l3.5-.4z"/></svg></div>
<div class="abs why-item left" style="left:111px;top:2314px"><h4>Proactive Asset Management</h4><p>Beyond operations, we actively enhance value, mitigate risk, and secure the right tenants.</p></div>
<div class="abs why-icon" style="left:405px;top:2332px"><svg width="22" height="22" viewBox="0 0 24 24" fill="none" stroke="#243240" stroke-width="1.4"><path d="M3 12l4-4 3 2 4-3 3 2 4 4-5 5-3-2-3 2z"/></svg></div>

<div class="abs emblem"><div class="brand"><span class="brand-dot" style="width:40px;height:40px"></span>Castellan Group</div></div>

<div class="abs why-icon" style="left:750px;top:2168px"><svg width="22" height="22" viewBox="0 0 24 24" fill="none" stroke="#243240" stroke-width="1.4"><circle cx="12" cy="12" r="3"/><path d="M12 2v3M12 19v3M2 12h3M19 12h3M5 5l2 2M17 17l2 2M5 19l2-2M17 7l2-2"/></svg></div>
<div class="abs why-item" style="left:821px;top:2152px"><h4>Bespoke Solutions</h4><p>Every property is unique. We craft customised management and leasing strategies aligned with your objectives and market conditions.</p></div>
<div class="abs why-icon" style="left:750px;top:2332px"><svg width="22" height="22" viewBox="0 0 24 24" fill="none" stroke="#243240" stroke-width="1.4"><path d="M7 11v9H3v-9zM7 19h9l3-7v-2h-6l1-5-2-1-5 7"/></svg></div>
<div class="abs why-item" style="left:821px;top:2314px"><h4>Professional Excellence</h4><p>Integrity, precision, and industry-leading best</p></div>

<a class="abs btn btn-orange" style="left:498px;top:2447px;width:204px;height:45px;justify-content:center">Book an Appraisal <svg viewBox="0 0 12 12" fill="none" stroke="#fff" stroke-width="1.4"><path d="M3 9l6-6M4 3h5v5"/></svg></a>

<div class="abs about-text">
  <div class="section-label">Who We Are</div>
  <h2>We Are Recognised As <span class="accent">A Trusted</span></h2>
  <p>At Castellan Group, we are recognised as a trusted authority in commercial and residential property management, sales, and leasing. Property owners, investors, and developers turn to us for our proven expertise, discretion, and consistent results.</p>
  <p>Our mission is to set the standard for excellence in property services. Guided by innovation, integrity, and strategic execution, we deliver outcomes that protect assets, maximise returns, and create enduring value for our clients.</p>
  <a class="btn btn-dark" style="margin-top:10px;height:41px">Schedule Consultation <svg viewBox="0 0 12 12" fill="none" stroke="#fff" stroke-width="1.4"><path d="M3 9l6-6M4 3h5v5"/></svg></a>
</div>
<div class="abs about-photo" role="img" aria-label="Handshake over a signed contract on a clipboard"></div>
<div class="abs divider"></div>

<div class="abs section-label center" style="top:3113px">Testimonials</div>
<h2 class="abs section-title center" style="top:3145px">What Our Clients Say <span class="accent">About Us</span></h2>

<div class="abs carousel-arrow" style="left:87px;background:#E4E7EB"><svg width="10" height="10" viewBox="0 0 10 10" fill="none" stroke="#fff" stroke-width="1.6"><path d="M6.5 2L3.5 5l3 3"/></svg></div>
<div class="abs carousel-arrow" style="left:1087px;background:var(--navy)"><svg width="10" height="10" viewBox="0 0 10 10" fill="none" stroke="#fff" stroke-width="1.6"><path d="M3.5 2l3 3-3 3"/></svg></div>

<article class="abs review" style="left:141px">
  <div class="quote">“</div>
  <div class="rating"><span class="stars">★★★★★</span><span class="source-mark"></span></div>
  <p>"Sed ut perspiciatis unde omnis iste natus error sit voluptatem accusantium laudantium, totam rem aperiam, eaque ipsa quae ab illo inventore veritatis architect"</p>
  <hr><h4>Elias Vance</h4><span>Asset Portfolio Manager</span>
</article>
<article class="abs review" style="left:459px">
  <div class="quote">“</div>
  <div class="rating"><span class="stars">★★★★★</span><span class="source-mark"></span></div>
  <p>"Sed ut perspiciatis unde omnis iste natus error sit voluptatem accusantium laudantium, totam rem aperiam, eaque ipsa quae ab illo inventore veritatis architect"</p>
  <hr><h4>Seraphina Hayes</h4><span>Senior Leasing Specialist</span>
</article>
<article class="abs review" style="left:776px">
  <div class="quote">“</div>
  <div class="rating"><span class="stars">★★★★★</span><span class="source-mark"></span></div>
  <p>"Sed ut perspiciatis unde omnis iste natus error sit voluptatem accusantium laudantium, totam rem aperiam, eaque ipsa quae ab illo inventore veritatis architect"</p>
  <hr><h4>Marcus Chen</h4><span>Regional Property Director</span>
</article>
<div class="abs dots"><i></i><i class="on"></i><i></i><i></i></div>

<section class="abs property">
  <div class="abs section-label center" style="top:82px">Commercial and Residential</div>
  <h2 class="abs section-title center" style="top:113px">Property Management &amp; <span class="accent">Leasing</span></h2>
  <article class="abs split-card card-commercial">
    <h3>Commercial Property</h3>
    <p class="sub">Trusted by medical centres, healthcare facilities, franchise brands, retail, and industrial investors.</p>
    <ul>
      <li><span class="tick"><svg width="9" height="9" viewBox="0 0 10 10" fill="none" stroke="#F0522E" stroke-width="1.8"><path d="M2 5l2 2 4-4"/></svg></span>Strategic Marketing &amp; Leasing</li>
      <li><span class="tick"><svg width="9" height="9" viewBox="0 0 10 10" fill="none" stroke="#F0522E" stroke-width="1.8"><path d="M2 5l2 2 4-4"/></svg></span>Tenant &amp; Lease Administration</li>
      <li><span class="tick"><svg width="9" height="9" viewBox="0 0 10 10" fill="none" stroke="#F0522E" stroke-width="1.8"><path d="M2 5l2 2 4-4"/></svg></span>Revenue Optimisation</li>
      <li><span class="tick"><svg width="9" height="9" viewBox="0 0 10 10" fill="none" stroke="#F0522E" stroke-width="1.8"><path d="M2 5l2 2 4-4"/></svg></span>Maintenance</li>
      <li><span class="tick"><svg width="9" height="9" viewBox="0 0 10 10" fill="none" stroke="#F0522E" stroke-width="1.8"><path d="M2 5l2 2 4-4"/></svg></span>Compliance &amp; Essential Services</li>
    </ul>
  </article>
  <article class="abs split-card card-residential" role="img" aria-label="Faded suburban home behind residential services list">
    <h3>Residential Property</h3>
    <p class="sub">Where Bayside Lifestyle Meets Property Excellence<br>Your Residential Experts.</p>
    <ul>
      <li><span class="tick"><svg width="9" height="9" viewBox="0 0 10 10" fill="none" stroke="#243240" stroke-width="1.8"><path d="M2 5l2 2 4-4"/></svg></span>Lifestyle-Driven Sales</li>
      <li><span class="tick"><svg width="9" height="9" viewBox="0 0 10 10" fill="none" stroke="#243240" stroke-width="1.8"><path d="M2 5l2 2 4-4"/></svg></span>Bayside &amp; Mornington Peninsula Specialists</li>
      <li><span class="tick"><svg width="9" height="9" viewBox="0 0 10 10" fill="none" stroke="#243240" stroke-width="1.8"><path d="M2 5l2 2 4-4"/></svg></span>Tailored Marketing</li>
      <li><span class="tick"><svg width="9" height="9" viewBox="0 0 10 10" fill="none" stroke="#243240" stroke-width="1.8"><path d="M2 5l2 2 4-4"/></svg></span>Negotiation Excellence</li>
      <li><span class="tick"><svg width="9" height="9" viewBox="0 0 10 10" fill="none" stroke="#243240" stroke-width="1.8"><path d="M2 5l2 2 4-4"/></svg></span>End-to-End Partnership</li>
    </ul>
  </article>
</section>
<div class="abs split-badge"><span style="width:16px;height:16px;border-radius:50%;background:var(--orange)"></span></div>

<form class="abs form-box">
  <label>Full Name</label><div class="field"></div>
  <label>Phone Number</label><div class="field"></div>
  <label>How can we help?</label><div class="field tall"></div>
  <div class="submit">Submit Now</div>
</form>

<div class="abs move-text">
  <h2>Ready to Make <span class="accent">Your Next Move?</span></h2>
  <p>Whether you're looking to buy a thriving enterprise or discreetly sell your business, Castellan Business Sales is your trusted partner.</p>
  <h3>At Castellan Group</h3>
  <div class="perk"><svg width="16" height="16" viewBox="0 0 16 16" fill="none" stroke="#2BA84A" stroke-width="2"><path d="M2 8l4 4 8-8"/></svg><div><h4>Complete Solution</h4><p>Australia's Trusted Business Sales &amp; M&amp;A Experts</p></div></div>
  <div class="perk"><svg width="16" height="16" viewBox="0 0 16 16" fill="none" stroke="#2BA84A" stroke-width="2"><path d="M2 8l4 4 8-8"/></svg><div><h4>Proven Results</h4><p>Maximise Your Exit With Precision And Discretion</p></div></div>
  <div class="perk"><svg width="16" height="16" viewBox="0 0 16 16" fill="none" stroke="#2BA84A" stroke-width="2"><path d="M2 8l4 4 8-8"/></svg><div><h4>Revenue Generation</h4><p>Discover Opportunities. Acquire With Confidence.</p></div></div>
</div>

<footer class="abs site-footer"></footer>
<div class="abs footer-bump"></div>
<svg class="abs to-top" width="30" height="22" viewBox="0 0 30 22" fill="none" stroke="#F0522E" stroke-width="2"><path d="M9 10l6-6 6 6M9 17l6-6 6 6"/></svg>

<div class="abs footer-about">
  <div class="brand"><span class="brand-dot" style="width:34px;height:34px"></span>Castellan Group</div>
  <p>Sed ut perspiciatis unde omnis iste natus error sit voluptatem accusantium dolorem.</p>
  <div class="follow">Follow Us: <i></i><i class="on"></i><i></i></div>
</div>

<div class="abs footer-col" style="left:418px;top:4966px">
  <h4>Quick Links</h4>
  <ul><li>Home</li><li>Commercial / Industrial</li><li>Residential</li><li>Business Sales ⌄</li><li>About Us</li><li>Contact us</li></ul>
</div>
<div class="abs footer-col" style="left:651px;top:4966px">
  <h4>Key Offerings</h4>
  <ul><li>Business listings</li><li>Appraisal report</li><li>What we do</li><li>Who we are</li></ul>
</div>
<div class="abs footer-col" style="left:838px;top:4966px;width:240px">
  <h4>Contact Us</h4>
  <div class="contact-line"><span class="contact-icon light"><svg width="14" height="14" viewBox="0 0 14 14" fill="none" stroke="#fff" stroke-width="1.3"><path d="M7 13s4-4 4-7.5a4 4 0 00-8 0C3 9 7 13 7 13z"/><circle cx="7" cy="5.5" r="1.4"/></svg></span><span>123, Lorem ipsum, dolor sit amet, adipiscing elit, 45</span></div>
  <div class="contact-line" style="align-items:center"><span class="contact-icon"><svg width="14" height="14" viewBox="0 0 14 14" fill="#fff"><path d="M3 1.5l2 .3.8 2.6-1.3 1a7 7 0 003.6 3.6l1-1.3 2.6.8.3 2c0 .6-.5 1-1 1A10 10 0 012 2.5c0-.5.4-1 1-1z"/></svg></span><span>Phone: (123) 456 7890</span></div>
  <div class="contact-line" style="align-items:center"><span class="contact-icon light"><svg width="14" height="14" viewBox="0 0 14 14" fill="none" stroke="#fff" stroke-width="1.3"><rect x="1.5" y="3" width="11" height="8"/><path d="M1.5 3l5.5 4.5L12.5 3"/></svg></span><span>info@castellangroup.com.au</span></div>
</div>

<div class="abs copyright">© 2023 Castellan Business Sales. All Rights Reserved.</div>

</body>
</html>
```